Web Design Project

Psychotherapy and Counselling Practice needs a landing page web design.

My business "Larkfield Advisory" specialises in the treatment of Anxiety and Depression with a holistic approach, endeavouring to unlock the key that holds us to ransom in a life that is imbalanced, frustrating, and ultimately of our own making due to our own perceptions and behaviours.

There is much that impacts us which we cannot change, but we are always in control of how we think, and how we frame our experiences.....learning to challenge those thoughts and behaviours that are destructive and disempowering opens up a world of joyful possibility. Life is about making choices, learn to make wiser and healthier choices.......

Larkfield Advisory has a client base of individual clients but will seek to expand to offer services to the Corporate world by offering an adjunct to employers for established "Wellness Programs".

Larkfield Advisory is a highly professional, ethically bound business, with the needs of the client at the forefront of all we do.

Larkfield Advisory wishes to avoid the usual "jargon driven" psychobabble offered on many counselling web pages. It aims to be stylishly presented, clean in look and with as few "words" as possible and a largely white background (faster loading and more powerful impact of what is stated), those words contained in the webpage should be meaningful, persuasive and have an impact simply at glance. Larkfield does not want , or expect, those prospective clients in need of support , to be reading through volumes of industry driven cliches.

At this point Larkfield is just looking for a high quality landing page. However in time this will likely expand to include other sections such as case studies, video content etc.

Target Market(s)

Those in need of emotional support, suffering mental health issues, and those simply wanting to become self aware supported by a mindful therapist.

Industry/Entity Type

Industry

Requirements
Must have
• The design must incorporate the Larkfield logo and colour schemes found on the attached files.

```html
<!DOCTYPE html>
<html lang="en">
<head>
<meta charset="utf-8">
<title>Larkfield Advisory</title>
<link rel="stylesheet" href="https://fonts.googleapis.com/css2?family=Questrial&family=Lora:ital@1&display=swap">
<style>
  :root{
    --green:#8aac12;
    --green-dark:#6f8d0a;
    --sky-top:#2b62b0;
    --sky-bottom:#4a8ad0;
    --ink:#333;
    --body:#444;
    --grey:#717171;
    --grey-dark:#5e5e5e;
    --panel:#f3f3f3;
    --panel-line:#d6d6d6;
    --white:#fff;
  }
  *{margin:0;padding:0;box-sizing:border-box}
  html,body{width:796px;height:1200px;overflow:hidden;background:var(--white)}
  body{font-family:"Questrial",sans-serif;color:var(--ink)}
  .page{position:relative;width:796px;height:1200px;overflow:hidden}
  .abs{position:absolute}

  .brand{left:92px;top:44px;font-size:17px;letter-spacing:.5px;color:var(--green)}
  .social{right:80px;top:11px;display:flex;gap:14px}
  .social span{width:22px;height:22px;border-radius:50%;background:var(--green);display:block}
  .nav{left:302px;top:53px;display:flex;font-size:11px;color:#555;letter-spacing:.3px}
  .nav a{color:inherit;text-decoration:none;margin-right:40px}
  .nav a:last-child{margin-right:0}

  .hero-waves{left:0;top:92px}
  .hero-photo{left:0;top:122px;width:796px;height:295px}
  .tagline{left:96px;top:302px;color:var(--white);font-size:13px;letter-spacing:2px;line-height:28px}
  .tagline b{font-weight:400;font-size:22px;letter-spacing:1.5px}
  .tagline .line2{padding-left:42px}

  .map{left:168px;top:436px;width:470px;height:214px;background:radial-gradient(ellipse at center,#eef3dc 0%,#f5f8ea 55%,rgba(255,255,255,0) 75%)}
  .mission{left:60px;width:676px;top:480px;text-align:center;font-size:23px;line-height:30px;color:#2e2e2e}
  .intro{left:80px;width:636px;top:553px;text-align:center;font-size:15.5px;line-height:21px;color:var(--body)}

  .quote-box{left:80px;top:652px;width:636px;height:117px;background:var(--panel);border:1px solid var(--panel-line);border-radius:3px}
  .quote{left:40px;right:40px;top:17px;text-align:center;font-family:"Lora",serif;font-style:italic;font-size:12.5px;line-height:19px;color:#444}
  .cta{left:246px;top:66px;width:143px;height:31px;background:var(--green);border:1px solid var(--green-dark);border-radius:3px;color:var(--white);font-size:14px;line-height:29px;text-align:center}

  .services-title{left:0;width:796px;top:797px;text-align:center;font-size:23px;color:#2e2e2e}
  .service{top:845px;width:210px;text-align:center}
  .service .icon{width:50px;height:50px;border-radius:50%;background:var(--green);margin:0 auto;display:flex;align-items:center;justify-content:center}
  .service h3{font-weight:400;font-size:13.5px;margin-top:17px;color:#222}
  .service p{font-size:10.5px;line-height:16px;margin-top:8px;color:var(--body)}

  .footer{left:0;top:1021px;width:796px;height:179px;background:var(--grey)}
  .footer h4{font-weight:400;font-size:13.5px;color:var(--white);margin-bottom:7px}
  .footer .col{top:20px;font-size:8px;line-height:13.5px;color:var(--white)}
  .footer ul{list-style:none}
  .footer em{display:block}
  .contact-row{display:flex}
  .contact-row span:first-child{width:32px}
  .footer-brand{left:603px;top:76px;font-size:18px;color:var(--white);letter-spacing:.5px}
  .footer-waves{left:0;top:1148px}
</style>
</head>
<body>
<div class="page">

  <header>
    <div class="abs brand">LARKFIELD</div>
    <div class="abs social" aria-label="Social links"><span></span><span></span><span></span></div>
    <nav class="abs nav">
      <a href="#">HOME</a><a href="#">ABOUT</a><a href="#">SERVICES</a><a href="#">TESTIMONIALS</a><a href="#">CONTACT</a>
    </nav>
  </header>

  <div class="abs hero-photo" role="img" aria-label="Woman leaping against a blue sky, trailing a long green scarf">
    <svg width="796" height="295" viewBox="0 0 796 295">
      <defs>
        <linearGradient id="sky" x1="0" y1="0" x2="0" y2="1">
          <stop offset="0" stop-color="var(--sky-top)"/>
          <stop offset="1" stop-color="var(--sky-bottom)"/>
        </linearGradient>
      </defs>
      <path d="M0 0 H796 V270 Q420 310 0 268 Z" fill="url(#sky)"/>
    </svg>
  </div>

  <svg class="abs hero-waves" width="796" height="50" viewBox="0 0 796 50">
    <path d="M0 20 Q400 50 796 22 V44 Q400 60 0 40 Z" fill="var(--sky-top)"/>
    <path d="M0 22 Q400 48 796 16 V26 Q400 50 0 30 Z" fill="var(--grey)"/>
    <path d="M66 5 Q300 30 648 9 Q330 28 66 5 Z" fill="var(--green)" stroke="var(--green)" stroke-width="3"/>
  </svg>

  <p class="abs tagline"><b>Life</b> is to short<br><span class="line2">to live in <b>unhappy</b> life...</span></p>

  <main>
    <div class="abs map" role="img" aria-label="Faint world map in pale green"></div>
    <h1 class="abs mission" style="font-weight:400">WE ARE HERE TO HELP SUPPORT ANYONE WHO WISHES<br>TO LIVE THE LIFE THAT IS TRUEST TO WHO THEY ARE</h1>
    <p class="abs intro">Research shows that more than half of the people around the world are not satisfied and happy with their life, we try to help people to find their happiness and make their life worth living.</p>

    <section class="abs quote-box">
      <p class="abs quote">There is much that impacts us which we cannot change, but we are always in control of how we think, and how we frame our experiences</p>
      <a class="abs cta" href="#">LET US HELP YOU</a>
    </section>

    <h2 class="abs services-title" style="font-weight:400">OUR SERVICES</h2>

    <div class="abs service" style="left:75px">
      <div class="icon"><svg width="24" height="22" viewBox="0 0 24 22"><path d="M3 2h18a2 2 0 0 1 2 2v9a2 2 0 0 1-2 2H11l-5 5v-5H3a2 2 0 0 1-2-2V4a2 2 0 0 1 2-2z" fill="#fff"/></svg></div>
      <h3>Consultant</h3>
      <p>We are here to listen to your problems, and ready to give some advises regarding your problems.</p>
    </div>
    <div class="abs service" style="left:293px">
      <div class="icon"><svg width="24" height="22" viewBox="0 0 24 22"><path d="M12 1 1 11h3v10h6v-6h4v6h6V11h3z" fill="#fff"/></svg></div>
      <h3>Treatment</h3>
      <p>We specialise in the treatment of Anxiety and Depression with a holistic approach.</p>
    </div>
    <div class="abs service" style="left:511px">
      <div class="icon"><svg width="24" height="22" viewBox="0 0 24 22"><path d="M12 21 2.5 11.5A5.5 5.5 0 0 1 12 4a5.5 5.5 0 0 1 9.5 7.5z" fill="#fff"/></svg></div>
      <h3>Wellness Program</h3>
      <p>We offer services to the Corporate world by offering a wellness program to employers</p>
    </div>
  </main>

  <footer class="abs footer">
    <div class="abs col" style="left:80px">
      <h4>Useful Links</h4>
      <ul><li>About us</li><li>Products</li><li>Services</li><li>Support</li><li>Contact us</li></ul>
    </div>
    <div class="abs col" style="left:204px;width:180px">
      <h4>What Our Clients Say</h4>
      <em>“Lorem Ipsum is simply dummy text of the printing and typesetting industry standard. Lorem Ipsum has been the industry dummy text ever since the 1500s”</em>
      Marianne
    </div>
    <div class="abs col" style="left:427px;width:170px">
      <h4>Contact Us</h4>
      <div class="contact-row"><span>Phone</span><span>: 014-555-0192</span></div>
      <div class="contact-row"><span>Fax</span><span>: 014-555-0192</span></div>
      <div class="contact-row"><span>E-mail</span><span>: hello@larkfield-advisory.com</span></div>
      <div class="contact-row"><span>Address</span><span>: Somewhere street, Zip Code,<br>&nbsp;&nbsp;City, Country</span></div>
    </div>
    <div class="abs footer-brand">LARKFIELD</div>
  </footer>

  <svg class="abs footer-waves" width="796" height="52" viewBox="0 0 796 52">
    <path d="M0 22 Q400 0 796 20 V52 H0 Z" fill="var(--white)"/>
    <path d="M0 30 Q400 10 796 28 V52 H0 Z" fill="var(--grey-dark)"/>
    <path d="M66 6 Q330 22 648 9 Q330 30 66 6 Z" fill="var(--green)"/>
  </svg>

</div>
</body>
</html>
```